Redesign website for small print company

Vindurgata is a small printing company in Iceland mainly servicing Students, schools, etc. We are also doing all kind of other jobs, like business cards, book printing, brochure printing etc. We are also selling books online.
Our website is: www.vindurgata.is
What we are looking for is:
- Web Design (Uncoded - PSD layout only)
- Mobile friendly design, using our current color scheme: Red, green, yellow and light gray.
- Clean simple design
- Simple, light and easy to use.
- More menu Items/drop down
Industry/Entity Type
Digital Printing
Number of Pages Required
5+ page
Requirements
Must have
- Easy navigation
- Designed for mobile
- Current color scheme (see logo)
Nice to have
- Icon based products

```html
<!DOCTYPE html>
<html lang="en">
<head>
<meta charset="utf-8">
<title>Vindurgata – Printing</title>
<link href="https://fonts.googleapis.com/css2?family=Lato:wght@400;700;900&family=Open+Sans:ital,wght@0,400;0,600;0,700;1,400&display=swap" rel="stylesheet">
<style>
:root{
  --red:#e4262c;
  --green:#17553a;
  --yellow:#f3c300;
  --light:#f2f2f2;
  --ink:#1f1f1f;
  --text:#666;
  --white:#fff;
}
*{box-sizing:border-box;margin:0;padding:0}
html,body{width:1200px;height:3516px;overflow:hidden}
body{font-family:'Open Sans',sans-serif;color:var(--ink);background:var(--white);position:relative}
/* top bar */
.topbar{position:absolute;top:0;left:0;width:1200px;height:38px;background:var(--red);color:#fff;font-size:14px}
.topbar .contact{position:absolute;left:98px;top:9px;display:flex;gap:14px;align-items:center}
.topbar .contact span{display:flex;align-items:center;gap:7px}
.topbar .langs{position:absolute;right:98px;top:11px;display:flex;gap:6px}
.topbar .langs i{display:block;width:24px;height:15px;border:1px solid #fff}
.topbar .langs i:first-child{background:#2d3f8f}
.topbar .langs i:last-child{background:#3b6fc4}
/* header */
.header{position:absolute;top:38px;left:0;width:1200px;height:108px;background:#fff}
.brand{position:absolute;display:flex;align-items:center;gap:12px;font-family:'Lato',sans-serif;font-weight:900;color:var(--ink)}
.header .brand{left:98px;top:30px;font-size:34px}
.brand .mark{width:46px;height:46px;background:var(--red)}
.nav{position:absolute;left:522px;top:44px;display:flex;gap:40px;font-family:'Lato',sans-serif;font-weight:700;font-size:17px}
.nav .active{color:var(--green)}
.header .tools{position:absolute;left:990px;top:32px;display:flex;gap:14px}
.tools .round{width:48px;height:48px;border-radius:50%;display:flex;align-items:center;justify-content:center}
.tools .outline{border:2px solid var(--green)}
.tools .solid{background:var(--green)}
.dropdown{position:absolute;left:842px;top:146px;width:133px;height:102px;background:#fff;box-shadow:0 3px 10px rgba(0,0,0,.18);padding:8px 22px;font-size:14px;line-height:29px;color:#444;z-index:3}
/* hero */
.hero{position:absolute;top:146px;left:0;width:1200px;height:531px;background:linear-gradient(100deg,#1a1a1a 0%,#3c3c3c 35%,#8a8a8a 60%,#6f7a6f 85%,#2a2f2a 100%)}
.hero h1{position:absolute;left:98px;top:128px;font-family:'Lato',sans-serif;font-weight:700;font-size:64px;color:#fff;letter-spacing:1px}
.hero p{position:absolute;left:100px;top:222px;width:560px;font-size:20px;line-height:34px;color:#fff}
.btn-outline{position:absolute;left:100px;top:330px;width:216px;height:61px;border:2px solid #fff;border-radius:31px;color:#fff;font-family:'Lato',sans-serif;font-weight:700;font-size:17px;display:flex;align-items:center;justify-content:center}
.dots{position:absolute;left:562px;top:456px;display:flex;gap:6px}
.dots i{width:14px;height:14px;border-radius:50%;border:2px solid #fff}
.dots i:first-child{background:#fff}
/* welcome */
.welcome{position:absolute;top:677px;left:0;width:1200px;height:490px}
.welcome .mark{position:absolute;left:98px;top:140px;width:60px;height:72px;background:var(--red)}
.welcome h2{position:absolute;left:98px;top:238px;font-family:'Lato',sans-serif;font-weight:700;font-size:42px;line-height:58px}
.welcome .copy{position:absolute;left:520px;top:78px;width:580px;font-size:14.5px;line-height:27px;color:var(--text)}
.welcome .copy p{margin-bottom:18px}
/* products */
.products{position:absolute;top:1167px;left:0;width:1200px;height:516px;background:var(--light)}
.section-title{position:absolute;left:0;width:1200px;text-align:center;font-family:'Lato',sans-serif;font-weight:700;font-size:42px}
.products .section-title{top:80px}
.product{position:absolute;top:200px;width:236px;text-align:center}
.product .icon{display:block;margin:0 auto;width:90px;height:95px;border-radius:6px}
.product h3{margin-top:30px;font-family:'Lato',sans-serif;font-weight:700;font-size:25px}
.product p{margin-top:14px;font-size:14.5px;line-height:23px;color:var(--text)}
.arrow{position:absolute;width:48px;height:48px;border-radius:50%;border:1.5px solid #999;display:flex;align-items:center;justify-content:center;background:#fff}
.arrow.onred{border-color:rgba(255,255,255,.7);background:transparent;width:36px;height:36px}
/* gallery */
.gallery{position:absolute;top:1683px;left:0;width:1200px;height:975px}
.gallery .section-title{top:82px}
.tile{position:absolute;width:319px;height:267px}
.btn-green{position:absolute;left:511px;top:820px;width:176px;height:59px;border-radius:30px;background:var(--green);color:#fff;font-family:'Lato',sans-serif;font-weight:700;font-size:17px;display:flex;align-items:center;justify-content:center}
/* testimonials */
.testimonials{position:absolute;top:2658px;left:0;width:1200px;height:436px;background:var(--red);color:#fff}
.testimonials .section-title{top:80px}
.quote{position:absolute;top:173px;width:330px}
.quote .avatar{position:absolute;left:0;top:0;width:71px;height:71px;border-radius:50%;background:#d9b8a0;border:3px solid #fff}
.quote blockquote{position:absolute;left:90px;top:0;width:240px;font-style:italic;font-size:13.5px;line-height:24px}
.quote blockquote b{font-size:22px;font-style:normal;margin-right:6px}
.quote .name{position:absolute;left:90px;top:124px;font-family:'Lato',sans-serif;font-weight:700;font-size:15px}
.quote .stars{position:absolute;left:90px;top:150px;color:var(--yellow);font-size:22px;letter-spacing:2px}
/* footer */
.footer{position:absolute;top:3094px;left:0;width:1200px;height:422px}
.footer .brand{left:98px;top:160px;font-size:32px}
.fcol{position:absolute;top:92px}
.fcol h4{font-family:'Lato',sans-serif;font-weight:700;font-size:17px;margin-bottom:24px}
.fcol.links{left:436px;font-size:13px;color:#555;line-height:24.5px}
.fcol.news{left:609px;width:260px;font-size:13px;color:#555;line-height:22px}
.news .field{margin-top:22px;border-bottom:1px solid #aaa;padding:6px 8px;font-size:12px;color:#999;width:255px}
.news .sub{margin-top:18px;width:102px;height:32px;border-radius:16px;background:var(--green);color:#fff;font-size:12px;font-weight:700;display:flex;align-items:center;justify-content:center}
.fcol.contact{left:942px;font-size:13px;color:#444;line-height:20px}
.contact .row{display:flex;gap:14px;margin-bottom:18px}
.footer hr{position:absolute;left:98px;top:326px;width:1004px;border:0;border-top:1px solid #ddd}
.footer .copyright{position:absolute;left:98px;top:361px;font-size:13px;color:#555}
.pay{position:absolute;top:356px;display:flex;gap:14px;left:783px}
.pay i{display:block;width:50px;height:28px;border-radius:4px;background:#444}
.social{position:absolute;top:350px;left:926px;display:flex;gap:10px}
.social i{display:block;width:36px;height:36px;border-radius:50%;border:1.5px solid var(--green)}
</style>
</head>
<body>

<div class="topbar">
  <div class="contact">
    <span><svg width="13" height="13" viewBox="0 0 24 24"><path fill="#fff" d="M6.6 10.8c1.4 2.8 3.8 5.1 6.6 6.6l2.2-2.2c.3-.3.7-.4 1-.2 1.1.4 2.3.6 3.6.6.6 0 1 .4 1 1V20c0 .6-.4 1-1 1C10.6 21 3 13.4 3 4c0-.6.4-1 1-1h3.5c.6 0 1 .4 1 1 0 1.3.2 2.5.6 3.6.1.3 0 .7-.2 1z"/></svg>555 0142</span>
    <span>|</span>
    <span><svg width="14" height="11" viewBox="0 0 24 18"><path fill="#fff" d="M0 0h24v2L12 10 0 2zM0 4l12 8 12-8v14H0z"/></svg>verk@vindurgata.is</span>
  </div>
  <div class="langs"><i></i><i></i></div>
</div>

<header class="header">
  <div class="brand"><span class="mark"></span>VINDURGATA</div>
  <nav class="nav"><span>HOME</span><span>SERVICES</span><span>JOB SUBMIT</span><span class="active">ABOUT US</span></nav>
  <div class="tools">
    <span class="round outline"><svg width="18" height="18" viewBox="0 0 24 24"><circle cx="10" cy="10" r="6.5" fill="none" stroke="#17553a" stroke-width="3"/><path d="M15 15l6 6" stroke="#17553a" stroke-width="3"/></svg></span>
    <span class="round solid"><svg width="20" height="18" viewBox="0 0 24 22"><path fill="#fff" d="M0 1h4l1 3h18l-3 9H7l-1 2h15v2H3l2.5-4L2 3H0z"/><circle cx="8" cy="20" r="2" fill="#fff"/><circle cx="18" cy="20" r="2" fill="#fff"/></svg></span>
  </div>
</header>

<div class="dropdown"><div>Who we are</div><div>Our Team</div><div>History</div></div>

<section class="hero" role="img" aria-label="Close-up photo of stacked printed booklets">
  <h1>VINDURGATA</h1>
  <p>Vindurgata is a small printing company in Iceland mainly servicing Students, schools, etc.</p>
  <span class="btn-outline">GET MORE INFO</span>
  <div class="dots"><i></i><i></i><i></i><i></i></div>
</section>

<section class="welcome">
  <span class="mark"></span>
  <h2>WELCOME TO<br>VINDURGATA</h2>
  <div class="copy">
    <p>University education is a company located in the campus, which has specialized in the service of school staff, as well as providing general public printing.</p>
    <p>Higher education publishes seminars and first-class textbooks for courses, prints theses for lesson, as well as working on an unprecedented number of smaller pieces for students, teachers and organizations. These include brochures, reports, questionnaires, business cards, books, OCR scanning and more.</p>
    <p>Higher education is a tailored print shop, The Leaf is the official eco-label of the Nordic countries, which has created a foothold in this country and is known among consumers.</p>
    <p>University education is located at the corner of Lyngbraut and Hafnarvegur. (walk in from Hafnarvegur)</p>
  </div>
</section>

<section class="products">
  <h2 class="section-title">OUR PRODUCTS</h2>
  <span class="arrow" style="left:25px;top:304px"><svg width="12" height="16" viewBox="0 0 12 16"><path d="M9 2L3 8l6 6" fill="none" stroke="#555" stroke-width="2"/></svg></span>
  <span class="arrow" style="left:1127px;top:304px"><svg width="12" height="16" viewBox="0 0 12 16"><path d="M3 2l6 6-6 6" fill="none" stroke="#555" stroke-width="2"/></svg></span>

  <div class="product" style="left:88px">
    <span class="icon" style="background:linear-gradient(160deg,#f3c300,#17553a 45%,#e4262c)" role="img" aria-label="Illustration of a stack of bound essays"></span>
    <h3>Essays</h3>
    <p>Higher education prints and binds essays. Theses are either woven, stapled, glued or bound</p>
  </div>
  <div class="product" style="left:348px">
    <span class="icon" style="background:linear-gradient(160deg,#17553a,#e4262c 55%)" role="img" aria-label="Illustration of business cards"></span>
    <h3>Business cards</h3>
    <p>Higher education prints and binds essays. Theses are either woven, stapled, glued or bound</p>
  </div>
  <div class="product" style="left:611px">
    <span class="icon" style="background:linear-gradient(90deg,#cfe0d6,#f6c9ca 50%,#fbeaa6)" role="img" aria-label="Illustration of a folded leaflet"></span>
    <h3>Leafleats</h3>
    <p>Higher education prints and binds essays. Theses are either woven, stapled, glued or bound</p>
  </div>
  <div class="product" style="left:873px">
    <span class="icon" style="background:linear-gradient(160deg,#f6c9ca,#e4262c)" role="img" aria-label="Illustration of a poster"></span>
    <h3>Posters</h3>
    <p>Higher education prints and binds essays. Theses are either woven, stapled, glued or bound</p>
  </div>
</section>

<section class="gallery">
  <h2 class="section-title">GALLERY</h2>
  <div class="tile" style="left:98px;top:188px;background:linear-gradient(135deg,#f4f1ea,#e6e1d4)" role="img" aria-label="Photo of bound thesis covers"></div>
  <div class="tile" style="left:441px;top:188px;background:linear-gradient(135deg,#d9d9d9,#7d7f8a)" role="img" aria-label="Photo of folded brochures with landscape prints"></div>
  <div class="tile" style="left:783px;top:188px;background:linear-gradient(135deg,#c4c4c4,#b85a5a 55%,#d9b340)" role="img" aria-label="Photo of printed book and magazine covers"></div>
  <div class="tile" style="left:98px;top:483px;background:linear-gradient(135deg,#d7d7cf,#c0407a 60%,#e6e6e6)" role="img" aria-label="Photo of a printed textbook"></div>
  <div class="tile" style="left:441px;top:483px;background:linear-gradient(135deg,#ececec,#3a3a3a 70%,#d2d2d2)" role="img" aria-label="Photo of rolled poster tubes"></div>
  <div class="tile" style="left:783px;top:483px;background:linear-gradient(135deg,#efefef,#d6d6d6)" role="img" aria-label="Photo of printed business cards"></div>
  <span class="btn-green">VIEW MORE</span>
</section>

<section class="testimonials">
  <h2 class="section-title">TESTIMONIALS</h2>
  <span class="arrow onred" style="left:29px;top:230px"><svg width="10" height="14" viewBox="0 0 12 16"><path d="M9 2L3 8l6 6" fill="none" stroke="#fff" stroke-width="2"/></svg></span>
  <span class="arrow onred" style="left:1134px;top:230px"><svg width="10" height="14" viewBox="0 0 12 16"><path d="M3 2l6 6-6 6" fill="none" stroke="#fff" stroke-width="2"/></svg></span>

  <div class="quote" style="left:98px">
    <div class="avatar" role="img" aria-label="Customer portrait"></div>
    <blockquote><b>“</b>Nam libero tempore, cum soluta nobis est eligendi optio cumque nihil impe dit quo minus id quod maxime placeat facere possimus, omnis</blockquote>
    <div class="name">LENA FARROW</div>
    <div class="stars">★★★★☆</div>
  </div>
  <div class="quote" style="left:450px">
    <div class="avatar" style="background:#9aa0a8" role="img" aria-label="Customer portrait"></div>
    <blockquote><b>“</b>Nam libero tempore, cum soluta nobis est eligendi optio cumque nihil impe dit quo minus id quod maxime placeat facere possimus, omnis</blockquote>
    <div class="name">TOM ESKILDSEN</div>
    <div class="stars">★★★★½</div>
  </div>
  <div class="quote" style="left:802px">
    <div class="avatar" style="background:#5a4036" role="img" aria-label="Customer portrait"></div>
    <blockquote><b>“</b>Nam libero tempore, cum soluta nobis est eligendi optio cumque nihil impe dit quo minus id quod maxime placeat facere possimus, omnis</blockquote>
    <div class="name">MIRA HOLLANDER</div>
    <div class="stars">★★★★☆</div>
  </div>
</section>

<footer class="footer">
  <div class="brand"><span class="mark"></span>VINDURGATA</div>
  <div class="fcol links">
    <h4>QUICK LINKS</h4>
    <div>Help</div><div>FAQ</div><div>Support</div><div>Sitemap</div><div>Terms Of Use</div><div>Privacy Statement</div>
  </div>
  <div class="fcol news">
    <h4>NEWSLETTER SUBSCRIPTION</h4>
    <div>Register your Email Address to get Information about us</div>
    <div class="field">Email Address</div>
    <div class="sub">SUBSCRIBE</div>
  </div>
  <div class="fcol contact">
    <h4>CONTACT US</h4>
    <div class="row"><svg width="12" height="16" viewBox="0 0 12 16"><path fill="#17553a" d="M6 0a6 6 0 0 1 6 6c0 4-6 10-6 10S0 10 0 6a6 6 0 0 1 6-6z"/><circle cx="6" cy="6" r="2" fill="#fff"/></svg><div>Lyngbraut 7<br>Reykjavik Iceland</div></div>
    <div class="row"><svg width="13" height="13" viewBox="0 0 24 24"><path fill="#17553a" d="M6.6 10.8c1.4 2.8 3.8 5.1 6.6 6.6l2.2-2.2c.3-.3.7-.4 1-.2 1.1.4 2.3.6 3.6.6.6 0 1 .4 1 1V20c0 .6-.4 1-1 1C10.6 21 3 13.4 3 4c0-.6.4-1 1-1h3.5c.6 0 1 .4 1 1 0 1.3.2 2.5.6 3.6.1.3 0 .7-.2 1z"/></svg><div>555 0142</div></div>
    <div class="row"><svg width="14" height="11" viewBox="0 0 24 18"><path fill="#17553a" d="M0 0h24v2L12 10 0 2zM0 4l12 8 12-8v14H0z"/></svg><div>verk@vindurgata.is</div></div>
  </div>
  <hr>
  <div class="copyright">Copyrights © 2018, Vindurgata. All rights reserved.</div>
  <div class="pay"><i></i><i></i></div>
  <div class="social"><i></i><i></i><i></i><i></i></div>
</footer>

</body>
</html>
```